Maple n Brook - Contact/Landing Page

I need a landing page which will essentially be the page that customers will go to from the 'website' link on QTV listing. It will provide a short overview of services which need to be selectable. a little further down can capture some contact details followed by a large Submit Now button etc...

I have some icon/logo's that can be utilised at the bottom of the page as industry type references.

Target Market(s)

End of Lease Cleaning Services

Industry/Entity Type

Cleaning Service

Colors

Designer to choose colors to be used in the design.

Requirements
Must have
• As per description
Should not have
• Colours to match my website maplenbrook.com.au

```html
<!DOCTYPE html>
<html lang="en">
<head>
<meta charset="utf-8">
<title>Maple n Brook – End of Lease Cleaning &amp; Pest Control</title>
<link rel="stylesheet" href="https://fonts.googleapis.com/css2?family=Crimson+Text:wght@400;700&family=IBM+Plex+Sans:wght@400&family=Libre+Baskerville:wght@700&family=Roboto:wght@400;500;700&display=swap">
<style>
  :root {
    --brand-blue: #2f68ae;
    --sky: #5bb1e6;
    --sky-pale: #cfe8f8;
    --ink: #1c1c1c;
    --text: #333333;
    --muted-bg: #f5f5f5;
    --line: #cfcfcf;
    --white: #ffffff;
    --watermark: #e2f1f7;
    --footer-a: #5db4e8;
    --footer-b: #3479c4;
  }
  * { box-sizing: border-box; margin: 0; padding: 0; }
  html, body { width: 718px; height: 1200px; overflow: hidden; }
  body { position: relative; background: var(--white); font-family: "IBM Plex Sans", Arial, sans-serif; color: var(--text); }

  /* Hero */
  .hero { position: absolute; left: 0; top: 0; width: 718px; height: 355px; background: var(--brand-blue); }
  .hotline { position: absolute; left: 60px; top: 11px; display: flex; gap: 6px; color: var(--white); font-family: "Roboto", Arial, sans-serif; }
  .hotline-text { line-height: 13px; }
  .hotline-title { font-size: 9px; font-weight: 500; }
  .hotline-phone { font-size: 10px; font-weight: 700; }
  .quote-btn { position: absolute; left: 569px; top: 10px; width: 88px; height: 25px; border: 1px solid var(--white); color: var(--white); font: 700 9.5px/23px "Roboto", Arial, sans-serif; text-align: center; }
  .brand-glow { position: absolute; left: 254px; top: 35px; width: 210px; height: 210px; border-radius: 50%; background: rgba(207, 232, 248, 0.16); }
  .brand-name { position: absolute; left: 0; top: 118px; width: 718px; text-align: center; font-family: "Crimson Text", Georgia, serif; font-weight: 400; font-size: 34px; line-height: 40px; color: var(--white); }
  .tagline { position: absolute; left: 0; top: 268px; width: 718px; text-align: center; color: var(--white); font-family: "Crimson Text", Georgia, serif; font-weight: 400; font-size: 22px; line-height: 28px; }

  /* Service cards */
  .card { position: absolute; top: 333px; width: 189px; height: 269px; background: var(--white); box-shadow: 0 1px 4px rgba(0,0,0,0.08); text-align: center; }
  .card-cleaning { left: 60px; }
  .card-carpet { left: 264px; }
  .card-pest { left: 469px; }
  .card-photo { position: relative; width: 189px; height: 137px; }
  .photo-cleaning { background: linear-gradient(135deg, #f2d04a 0%, #3f8fd6 40%, #c9504a 75%, #8d5bbf 100%); }
  .photo-carpet { background: linear-gradient(135deg, #8c8c8c 0%, #d4d0c8 45%, #bdb8ae 100%); }
  .photo-pest { background: linear-gradient(135deg, #ecd4b2 0%, #d8b48a 50%, #b98a5c 100%); }
  .card-notch { position: absolute; left: 0; bottom: 0; }
  .card-icon { position: absolute; left: 74px; top: 96px; width: 42px; height: 42px; border-radius: 50%; background: var(--brand-blue); border: 2px solid var(--white); display: flex; align-items: center; justify-content: center; }
  .card-title { margin-top: 9px; font-family: "Crimson Text", Georgia, serif; font-weight: 400; font-size: 20px; color: var(--ink); line-height: 24px; }
  .card-text { margin: 4px auto 0; width: 158px; font-size: 11px; line-height: 16.7px; color: var(--text); }
  .select-btn { position: absolute; left: 38px; top: 230px; width: 112px; height: 29px; background: linear-gradient(90deg, var(--brand-blue) 0%, var(--sky) 100%); color: var(--white); font: 500 10px/29px "Roboto", Arial, sans-serif; display: flex; align-items: center; justify-content: center; gap: 5px; }

  /* Contact */
  .contact { position: absolute; left: 0; top: 660px; width: 718px; height: 313px; background: var(--muted-bg); overflow: hidden; }
  .contact-watermark { position: absolute; left: 505px; top: 238px; font-family: "Crimson Text", Georgia, serif; font-weight: 400; font-size: 32px; line-height: 40px; color: var(--watermark); white-space: nowrap; }
  .contact-heading { position: absolute; left: 115px; top: 68px; font-family: "Libre Baskerville", Georgia, serif; font-weight: 700; font-size: 20px; color: var(--ink); }
  .field { position: absolute; left: 115px; width: 268px; height: 27px; display: flex; align-items: center; }
  .field label { width: 60px; font-family: "Roboto", Arial, sans-serif; font-size: 10px; color: var(--ink); }
  .field .input { width: 209px; height: 27px; background: var(--white); border: 1px solid var(--line); }
  .contact-email { position: absolute; left: 418px; top: 94px; display: flex; align-items: center; gap: 8px; }
  .contact-email-text { font: 700 10px/17px "Roboto", Arial, sans-serif; color: var(--ink); }
  .submit-btn { position: absolute; left: 419px; top: 133px; width: 80px; height: 28px; background: linear-gradient(90deg, var(--brand-blue) 0%, var(--sky) 100%); color: var(--white); font: 500 10px/28px "Roboto", Arial, sans-serif; text-align: center; }
  .contact-row { position: absolute; left: 419px; display: flex; align-items: center; gap: 8px; font: 500 11.5px/18px "Roboto", Arial, sans-serif; color: var(--ink); }
  .contact-dot { width: 25px; height: 25px; border-radius: 50%; background: var(--white); display: flex; align-items: center; justify-content: center; flex: none; }

  /* Clients */
  .clients-heading { position: absolute; left: 0; top: 1013px; width: 718px; text-align: center; font-family: "Libre Baskerville", Georgia, serif; font-weight: 700; font-size: 20px; color: var(--ink); }
  .client-badge { position: absolute; top: 1057px; height: 37px; }

  /* Footer */
  .footer { position: absolute; left: 0; top: 1155px; width: 718px; height: 45px; background: linear-gradient(90deg, var(--footer-a) 0%, var(--footer-b) 100%); color: var(--white); font-family: "Roboto", Arial, sans-serif; }
  .footer-copy { position: absolute; left: 60px; top: 15px; font-size: 9.5px; }
  .footer-social { position: absolute; left: 346px; top: 9px; width: 26px; height: 26px; border: 1px solid var(--white); border-radius: 50%; }
  .footer-licence { position: absolute; right: 60px; top: 14px; font-size: 11px; }
</style>
</head>
<body>

<header class="hero">
  <div class="hotline">
    <svg width="24" height="24" viewBox="0 0 24 24" fill="none" stroke="#fff" stroke-width="1.2" aria-hidden="true">
      <circle cx="11" cy="10" r="6"/><path d="M4 20c2-3 5-4 7-4s5 1 7 4"/><rect x="16" y="1" width="7" height="5" rx="1"/>
    </svg>
    <div class="hotline-text">
      <div class="hotline-title">HOUSE CLEANING AND PEST CONTROL</div>
      <div class="hotline-phone">CALL / SMS 0400 555 318</div>
    </div>
  </div>
  <div class="quote-btn">GET A QUOTE</div>
  <div class="brand-glow" aria-hidden="true"></div>
  <div class="brand-name">Maple n Brook</div>
  <h1 class="tagline">End of Lease Cleaning &nbsp;|&nbsp; Licensed Pest Control</h1>
</header>

<article class="card card-cleaning">
  <div class="card-photo photo-cleaning" role="img" aria-label="Cleaning supplies: buckets, spray bottles, broom and dustpan">
    <svg class="card-notch" width="189" height="16" viewBox="0 0 189 16" aria-hidden="true"><polygon points="0,16 94.5,1 189,16" fill="#fff"/><polyline points="0,16 94.5,1 189,16" fill="none" stroke="#2f68ae" stroke-width="2"/></svg>
    <div class="card-icon">
      <svg width="22" height="22" viewBox="0 0 22 22" fill="none" stroke="#fff" stroke-width="1.2" aria-hidden="true"><path d="M3 10h7l-1 10H4z"/><path d="M5 10V6h3v4"/><path d="M12 12h7l-1 8h-5z"/><path d="M12.5 12c0-2 6-2 6 0"/><path d="M17 3l.5 1.5L19 5l-1.5.5L17 7l-.5-1.5L15 5l1.5-.5z"/></svg>
    </div>
  </div>
  <h2 class="card-title">Cleaning</h2>
  <p class="card-text">All interior cleaning carried out to property management requirements</p>
  <div class="select-btn">SELECT <svg width="10" height="10" viewBox="0 0 10 10" aria-hidden="true"><rect x="0.7" y="0.7" width="8.6" height="8.6" fill="none" stroke="#fff" stroke-width="1.2"/></svg></div>
</article>

<article class="card card-carpet">
  <div class="card-photo photo-carpet" role="img" aria-label="Vacuum cleaner on a pale carpet">
    <svg class="card-notch" width="189" height="16" viewBox="0 0 189 16" aria-hidden="true"><polygon points="0,16 94.5,1 189,16" fill="#fff"/><polyline points="0,16 94.5,1 189,16" fill="none" stroke="#2f68ae" stroke-width="2"/></svg>
    <div class="card-icon">
      <svg width="22" height="22" viewBox="0 0 22 22" fill="none" stroke="#fff" stroke-width="1.2" aria-hidden="true"><path d="M3 10h7l-1 10H4z"/><path d="M5 10V6h3v4"/><path d="M12 12h7l-1 8h-5z"/><path d="M12.5 12c0-2 6-2 6 0"/><path d="M17 3l.5 1.5L19 5l-1.5.5L17 7l-.5-1.5L15 5l1.5-.5z"/></svg>
    </div>
  </div>
  <h2 class="card-title">Carpet Cleaning</h2>
  <p class="card-text">Carpet stacam cleaning to Australian Standard As 3733:1995</p>
  <div class="select-btn">SELECT <svg width="10" height="10" viewBox="0 0 10 10" aria-hidden="true"><rect x="0.7" y="0.7" width="8.6" height="8.6" fill="none" stroke="#fff" stroke-width="1.2"/><polyline points="2.5,5 4.3,7 8.5,2" fill="none" stroke="#fff" stroke-width="1.3"/></svg></div>
</article>

<article class="card card-pest">
  <div class="card-photo photo-pest" role="img" aria-label="Dead cockroach on a wooden surface">
    <svg class="card-notch" width="189" height="16" viewBox="0 0 189 16" aria-hidden="true"><polygon points="0,16 94.5,1 189,16" fill="#fff"/><polyline points="0,16 94.5,1 189,16" fill="none" stroke="#2f68ae" stroke-width="2"/></svg>
    <div class="card-icon">
      <svg width="22" height="22" viewBox="0 0 22 22" fill="none" stroke="#fff" stroke-width="1.2" aria-hidden="true"><path d="M3 10h7l-1 10H4z"/><path d="M5 10V6h3v4"/><path d="M12 12h7l-1 8h-5z"/><path d="M12.5 12c0-2 6-2 6 0"/><path d="M17 3l.5 1.5L19 5l-1.5.5L17 7l-.5-1.5L15 5l1.5-.5z"/></svg>
    </div>
  </div>
  <h2 class="card-title">Pest Control</h2>
  <p class="card-text">Mandatory requirement for pets on premises</p>
  <div class="select-btn">SELECT <svg width="10" height="10" viewBox="0 0 10 10" aria-hidden="true"><rect x="0.7" y="0.7" width="8.6" height="8.6" fill="none" stroke="#fff" stroke-width="1.2"/></svg></div>
</article>

<section class="contact">
  <div class="contact-watermark" aria-hidden="true">Maple n Brook</div>
  <h2 class="contact-heading">HOW CAN WE HELP YOU?</h2>
  <div class="field" style="top:99px"><label>First Name*</label><div class="input"></div></div>
  <div class="field" style="top:132px"><label>sur Name*</label><div class="input"></div></div>
  <div class="field" style="top:165px"><label>Email*</label><div class="input"></div></div>
  <div class="field" style="top:198px"><label>Phone*</label><div class="input"></div></div>
  <div class="field" style="top:231px"><label>Suburb*</label><div class="input"></div></div>

  <div class="contact-email">
    <svg width="35" height="25" viewBox="0 0 35 25" aria-hidden="true"><rect x="1" y="1" width="33" height="23" fill="none" stroke="#2f68ae" stroke-width="2"/><polyline points="1,1 17.5,14 34,1" fill="none" stroke="#2f68ae" stroke-width="2"/><path d="M1 24 13 11M22 11 34 24" fill="none" stroke="#2f68ae" stroke-width="2"/></svg>
    <div class="contact-email-text">EMAIL US<br>INFO@MAPLENBROOK.COM.AU</div>
  </div>
  <div class="submit-btn">SUBMIT</div>
  <div class="contact-row" style="top:174px">
    <div class="contact-dot"><svg width="9" height="12" viewBox="0 0 9 12" aria-hidden="true"><path d="M4.5 0C2 0 0 2 0 4.4 0 7.6 4.5 12 4.5 12S9 7.6 9 4.4C9 2 7 0 4.5 0z" fill="#2f68ae"/><circle cx="4.5" cy="4.4" r="1.6" fill="#fff"/></svg></div>
    <div>24 Lantern Ct, Riverside NSW<br>2199, Australia</div>
  </div>
  <div class="contact-row" style="top:215px">
    <div class="contact-dot"><svg width="12" height="12" viewBox="0 0 12 12" aria-hidden="true"><path d="M2.5 0.8 4.4 3 3.4 4.4C4 6 5.8 7.8 7.5 8.6L8.9 7.6 11.2 9.5 10 11.4C5.5 11 1 6.5 0.6 2z" fill="#2f68ae"/></svg></div>
    <div>0400 555 318</div>
  </div>
</section>

<h2 class="clients-heading">OUR CLIENTS</h2>
<div class="client-badge" style="left:57px;width:91px;background:#1e1e1e;border-radius:3px" role="img" aria-label="Certification partner badge"></div>
<div class="client-badge" style="left:193px;width:110px;background:linear-gradient(90deg,#2e3f8f,#c8323c)" role="img" aria-label="Systems partner badge"></div>
<div class="client-badge" style="left:357px;width:63px;background:#26356f" role="img" aria-label="Training partner badge"></div>
<div class="client-badge" style="left:455px;width:114px;top:1060px;height:34px;background:#86b543" role="img" aria-label="Environmental studies partner badge"></div>
<div class="client-badge" style="left:597px;width:61px;background:#1a3f7a" role="img" aria-label="Environment authority badge"></div>

<footer class="footer">
  <div class="footer-copy">© 2021 Maple n Brook. All Rights Reserved</div>
  <div class="footer-social" role="img" aria-label="Social media link"></div>
  <div class="footer-licence">PEST LICENCE: 4817263</div>
</footer>

</body>
</html>
```